Website for IT technology distribution company

Small business distributor of remote IT/Telecoms technology services in Canada

Looking for a bold, clean and professional design for WordPress. We would like a web site design from a designer who may be able to help us upload the site to WordPress (Ideally CSS files).
The website will have the following pages:
1) Home
2) Register
3) Packages
4) Contact

I am also attaching the company logo (with sourcefile, images for page 1 and details on wording/content for website)

Design must use colors that compliment the logo

Must Have:
- Must contain the logo in the header

Should Not Have:
- must not be blog or magazine style layout or look and feel

Industry/Entity Type

Business

```html
<!DOCTYPE html>
<html lang="en">
<head>
<meta charset="utf-8">
<title>Register</title>
<link href="https://fonts.googleapis.com/css2?family=Montserrat:wght@300;400;700&family=Open+Sans:wght@600;700&display=swap" rel="stylesheet">
<style>
:root{
  --page-bg:#f2f2f2;
  --band-pink:#f3dfe1;
  --title:#6b7589;
  --label:#6b7589;
  --accent-red:#ff2a2a;
  --panel-bg:#e9e7e7;
  --panel-border:#d3d2d2;
  --field-bg:#efeeee;
  --field-border:#b8bcc6;
  --select-bg:#ffffff;
  --arrow-box:#7b8494;
  --button:#7b8494;
  --button-edge:#4c5261;
  --quote:#ffffff;
}
*{box-sizing:border-box;margin:0;padding:0}
html,body{width:1200px;height:1087px;overflow:hidden}
body{
  position:relative;
  background:linear-gradient(to bottom,var(--band-pink) 0,var(--page-bg) 44px,var(--page-bg) 100%);
  font-family:"Montserrat",Arial,sans-serif;
  color:var(--label);
}
.page-title{
  position:absolute;left:173px;top:10px;
  font-family:"Montserrat",Arial,sans-serif;font-weight:700;
  font-size:36px;letter-spacing:1px;color:var(--title);
}
.promo{
  position:absolute;left:175px;width:277px;height:227px;
  border-top:6px solid var(--accent-red);
  box-shadow:-6px 8px 12px rgba(0,0,0,.35);
  overflow:hidden;
}
.promo-photo{position:absolute;inset:0}
.promo--phone{top:63px}
.promo--phone .promo-photo{background:linear-gradient(120deg,#4a5253 0%,#6b7373 45%,#d9d6d6 80%,#f4eeee 100%)}
.promo--servers{top:336px}
.promo--servers .promo-photo{background:linear-gradient(160deg,#5a4e3a 0%,#2a2520 45%,#141210 100%)}
.promo--keyboard{top:609px;left:174px}
.promo--keyboard .promo-photo{background:linear-gradient(170deg,#8a8a98 0%,#262a44 35%,#141628 70%,#2a2e5a 100%)}
.promo-quote{
  position:absolute;left:6px;right:6px;
  font-family:"Open Sans",Arial,sans-serif;font-weight:700;
  font-size:15.5px;line-height:23px;color:var(--quote);
  text-shadow:0 1px 3px rgba(0,0,0,.6);
}
.promo--phone .promo-quote{top:80px;font-weight:600}
.promo--servers .promo-quote{top:104px;font-weight:600;font-size:16.5px}
.promo--keyboard .promo-quote{top:118px;font-weight:600;font-size:16.5px}

.register-panel{
  position:absolute;left:490px;top:62px;width:554px;height:993px;
  background:var(--panel-bg);border:1px solid var(--panel-border);
  padding:12px 0 0 29px;
}
.required-note{
  font-size:13.5px;font-style:italic;color:var(--accent-red);
  line-height:16px;margin-bottom:15px;font-weight:400;
}
.field-grid{
  display:grid;grid-template-columns:227px 227px;column-gap:50px;row-gap:20px;
}
.field{display:flex;flex-direction:column}
.field--wide{grid-column:1 / span 2}
.field-label{font-size:12.5px;line-height:16px;margin-bottom:1px;font-weight:400;letter-spacing:.2px}
.text-input{
  height:28px;background:var(--field-bg);border:1px solid var(--field-border);
}
.text-area{height:87px;background:var(--field-bg);border:1px solid var(--field-border)}
.select-input{
  position:relative;height:28px;background:var(--select-bg);border:1px solid var(--field-border);
  font-size:12.5px;line-height:26px;padding-left:9px;color:#2b2f38;
}
.select-arrow{
  position:absolute;right:1px;top:1px;width:26px;height:24px;background:var(--arrow-box);
}
.select-arrow svg{position:absolute;left:8px;top:8px}
.send-button{
  display:flex;align-items:center;justify-content:center;gap:12px;
  margin:19px 0 0 210px;width:131px;height:35px;
  background:var(--button);border-bottom:4px solid var(--button-edge);border-radius:3px;
  color:#fff;font-size:12.5px;
}
</style>
</head>
<body>
<h1 class="page-title">REGISTER</h1>

<aside>
  <figure class="promo promo--phone">
    <div class="promo-photo" role="img" aria-label="Photo of a desk IP telephone"></div>
    <p class="promo-quote">“Save up to 90% over traditional, on-site, engineering methods”</p>
  </figure>
  <figure class="promo promo--servers">
    <div class="promo-photo" role="img" aria-label="Photo of a rack of server drives"></div>
    <p class="promo-quote">“Why pay a CORVEX engineer to sit and wait for work when you can have one when you need one and pay for only what you use”</p>
  </figure>
  <figure class="promo promo--keyboard">
    <div class="promo-photo" role="img" aria-label="Photo of a computer keyboard close-up"></div>
    <p class="promo-quote">“Why put off until tomorrow what you can do today? Pay by the hour and have it done today”</p>
  </figure>
</aside>

<section class="register-panel">
  <p class="required-note">All field are required</p>
  <div class="field-grid">
    <div class="field"><span class="field-label">First Name</span><div class="text-input"></div></div>
    <div class="field"><span class="field-label">Last Name</span><div class="text-input"></div></div>
    <div class="field"><span class="field-label">Name of Company</span><div class="text-input"></div></div>
    <div class="field"><span class="field-label">Email</span><div class="text-input"></div></div>
    <div class="field"><span class="field-label">Phone Number</span><div class="text-input"></div></div>
    <div class="field"><span class="field-label">Street</span><div class="text-input"></div></div>
    <div class="field"><span class="field-label">City</span><div class="text-input"></div></div>
    <div class="field"><span class="field-label">State</span><div class="text-input"></div></div>
    <div class="field"><span class="field-label">Postal Code</span><div class="text-input"></div></div>
    <div class="field"><span class="field-label">Country</span>
      <div class="select-input">Please select one<span class="select-arrow"><svg width="10" height="8" viewBox="0 0 10 8"><path d="M0 0h10L5 8z" fill="#fff"/></svg></span></div></div>
    <div class="field"><span class="field-label">Proposed Partnership Scheme</span>
      <div class="select-input">Please select one<span class="select-arrow"><svg width="10" height="8" viewBox="0 0 10 8"><path d="M0 0h10L5 8z" fill="#fff"/></svg></span></div></div>
    <div class="field"><span class="field-label">Year Established</span><div class="text-input"></div></div>
    <div class="field"><span class="field-label">Corvex Partnership Level</span>
      <div class="select-input">Please select one<span class="select-arrow"><svg width="10" height="8" viewBox="0 0 10 8"><path d="M0 0h10L5 8z" fill="#fff"/></svg></span></div></div>
    <div class="field"><span class="field-label">Turnover (estimate)</span><div class="text-input"></div></div>
    <div class="field"><span class="field-label">Average Growth Rate (p/annum)</span><div class="text-input"></div></div>
    <div class="field"><span class="field-label">Number of Staff</span><div class="text-input"></div></div>
    <div class="field field--wide"><span class="field-label">Regions/Countries you currently work in</span><div class="text-area"></div></div>
    <div class="field"><span class="field-label">Average Client Size</span>
      <div class="select-input">Please select one<span class="select-arrow"><svg width="10" height="8" viewBox="0 0 10 8"><path d="M0 0h10L5 8z" fill="#fff"/></svg></span></div></div>
    <div class="field"><span class="field-label">Average Spend per Client (estimate)</span><div class="text-input"></div></div>
    <div class="field field--wide"><span class="field-label">What Sectors do you Currently Work within?</span><div class="text-area"></div></div>
    <div class="field"><span class="field-label">Are You Looking to Expand in 2014</span>
      <div class="select-input">Please select one<span class="select-arrow"><svg width="10" height="8" viewBox="0 0 10 8"><path d="M0 0h10L5 8z" fill="#fff"/></svg></span></div></div>
    <div class="field"><span class="field-label">Referral Code (or "N/A")</span><div class="text-input"></div></div>
  </div>
  <div class="send-button">Send
    <svg width="18" height="8" viewBox="0 0 18 8"><path d="M0 4h16M12 1l4 3-4 3" stroke="#fff" stroke-width="1.4" fill="none"/></svg>
  </div>
</section>
</body>
</html>
```